Bramblewood Card Company Business Cards

We are a trading card store with Glimmorax, sports and other TCG cards, we need a business card design that encompasses a clean cut, modern style with a retro flare. website is bramblewoodcardco.com for reference. Can utilize a comic book era feel or a more modern outdoor feel to utilize the "Pacific Northwest" elements of tress, mountains, etc.

Industry/Entity Type

Trading cards and collectibles

Contact Information for Business Card

business name, email address, phone number, name, owner job title

Font styles to use
Sans Serif

```html
<!DOCTYPE html>
<html lang="en">
<head>
<meta charset="utf-8">
<title>Bramblewood Card Company – Business Card</title>
<link href="https://fonts.googleapis.com/css2?family=Arimo:wght@400;700&display=swap" rel="stylesheet">
<style>
  :root {
    --bg: #1c1c1e;
    --paper: #f7f7f5;
    --brand-blue: #0aaed6;
    --brand-blue-deep: #0690b5;
    --slate: #6b6b6d;
    --ink: #555558;
    --rule: #707072;
  }
  * { box-sizing: border-box; margin: 0; padding: 0; }
  html, body {
    width: 1200px; height: 963px; overflow: hidden;
    background: var(--bg);
    font-family: "Arimo", Arial, sans-serif;
  }
  .stage { position: relative; width: 1200px; height: 963px; }
  .card {
    position: absolute; left: 340px;
    width: 520px; height: 297px;
    border-radius: 22px; overflow: hidden;
  }
  .card--front { top: 150px; background: var(--paper); }
  .card--back {
    top: 516px;
    background: linear-gradient(160deg, var(--brand-blue) 0%, #09a6cf 55%, var(--brand-blue-deep) 100%);
  }

  .contact { position: absolute; left: 36px; top: 70px; width: 300px; }
  .contact__name {
    color: var(--brand-blue); font-weight: 700; font-size: 22px;
    text-transform: uppercase; letter-spacing: 0.2px;
  }
  .contact__title { color: var(--ink); font-size: 14px; margin-top: 2px; }
  .contact__rule {
    position: absolute; left: 36px; top: 128px;
    width: 440px; height: 1px; background: var(--rule);
  }
  .contact__list { list-style: none; margin-top: 28px; }
  .contact__item {
    display: flex; align-items: center; gap: 9px;
    color: var(--ink); font-size: 14px; margin-bottom: 6px;
  }
  .contact__icon { width: 14px; height: 14px; flex: none; }

  .brand {
    position: absolute; right: 36px; top: 38px; width: 190px;
    display: flex; align-items: center; gap: 10px;
  }
  .brand__dot {
    width: 14px; height: 14px; border-radius: 50%;
    background: var(--slate); flex: none;
  }
  .brand__name {
    color: var(--slate); font-weight: 700; font-size: 17px;
    line-height: 1.2; text-transform: uppercase; letter-spacing: 1px;
  }

  .edge-band { position: absolute; left: 0; bottom: 0; width: 520px; height: 26px; }

  .back-brand {
    position: absolute; inset: 0;
    display: flex; align-items: center; justify-content: center;
    padding: 0 40px;
  }
  .back-brand__name {
    color: #ffffff; font-weight: 700; font-size: 30px; line-height: 1.2;
    text-align: center; letter-spacing: 2px; text-transform: uppercase;
  }
</style>
</head>
<body>
<main class="stage">
  <section class="card card--front" aria-label="Business card front">
    <div class="contact">
      <h1 class="contact__name">Daniel Harlow</h1>
      <p class="contact__title">Manager</p>
      <ul class="contact__list">
        <li class="contact__item">
          <svg class="contact__icon" viewBox="0 0 16 16" aria-hidden="true">
            <path d="M4 1.5l2 3-1.3 1.3c.8 1.8 2.2 3.2 4 4L10 8.5l3 2-1.3 2.5C7 13 3 9 3 3.6z" fill="none" stroke="#0aaed6" stroke-width="1.5" stroke-linejoin="round"/>
          </svg>
          <span>555-014-2100</span>
        </li>
        <li class="contact__item">
          <svg class="contact__icon" viewBox="0 0 16 16" aria-hidden="true">
            <rect x="1" y="3" width="14" height="10" rx="1.5" fill="none" stroke="#0aaed6" stroke-width="1.5"/>
            <path d="M1.5 4l6.5 5 6.5-5" fill="none" stroke="#0aaed6" stroke-width="1.5"/>
          </svg>
          <span>info@bramblewoodcardco.com</span>
        </li>
      </ul>
    </div>
    <div class="contact__rule"></div>

    <div class="brand">
      <span class="brand__dot"></span>
      <span class="brand__name">Bramblewood<br>Card Company</span>
    </div>

    <svg class="edge-band" viewBox="0 0 520 26" preserveAspectRatio="none" aria-hidden="true">
      <polygon points="0,12 250,12 262,26 0,26" fill="var(--brand-blue)"/>
      <polygon points="250,12 262,12 275,0 520,0 520,26 262,26" fill="var(--slate)"/>
    </svg>
  </section>

  <section class="card card--back" aria-label="Business card back">
    <div class="back-brand">
      <span class="back-brand__name">Bramblewood<br>Card Company</span>
    </div>
  </section>
</main>
</body>
</html>
```